BUSINESS CARD - HALLORAN FIELD SERVICES

I would like to create a business card for my fertilizer spreading business. I would like to incorporate my existing logo and also a description of the services offered. The business card will be given to farmers so must be kept simple but effective. It will also be left in stores so much also be eye catching in order to stand out from other cards.

Target Market(s)

FARMERS

Requirements
Must have
• FRONT OF CARD = EXISTING LOGO + "CUSTOMISED SPREADING" below the logo

REAR Of CARD = SERVICES OFFERED AND CONTACT DETAILS

- Bulk fertilizer including Lime, Gypsum, Manure & Compost
- Granular fertilizer including Single Super, Urea, Gran-am, & Custom Blends
- Modern equipment - Autosteer & Variable Rate Capable
- Friendly & Reliable Service
- Contact Gus: 0417 552 308
Nice to have
• utilize same color scheme as existing logo

```html
<!DOCTYPE html>
<html lang="en">
<head>
<meta charset="utf-8">
<title>Halloran Field Services – Business Card</title>
<link href="https://fonts.googleapis.com/css2?family=Lato:wght@400;700;900&display=swap" rel="stylesheet">
<style>
  :root {
    --backdrop: #3a3c40;
    --card-dark: #000000;
    --card-light: #ffffff;
    --brand-grey: #7a7a7a;
    --brand-orange: #f7931e;
    --text-dark: #3c3c3c;
  }
  * { box-sizing: border-box; margin: 0; padding: 0; }
  html, body {
    width: 1200px;
    height: 900px;
    overflow: hidden;
  }
  body {
    background: var(--backdrop);
    font-family: "Lato", sans-serif;
    position: relative;
  }
  .card {
    position: absolute;
    left: 300px;
    width: 600px;
    height: 343px;
    border-radius: 16px;
    box-shadow: 0 10px 30px rgba(0,0,0,0.45);
    overflow: hidden;
  }
  .card--front {
    top: 60px;
    background: var(--card-dark);
    display: flex;
    flex-direction: column;
    align-items: center;
    justify-content: center;
  }
  .brand-dot {
    width: 110px;
    height: 110px;
    border-radius: 50%;
    background: var(--brand-grey);
    margin-bottom: 22px;
  }
  .brand-name {
    font-weight: 900;
    font-size: 40px;
    letter-spacing: 0.5px;
    color: var(--brand-grey);
    text-align: center;
    line-height: 1.05;
    white-space: nowrap;
  }
  .tagline {
    display: flex;
    align-items: center;
    gap: 14px;
    margin-top: 12px;
    width: 470px;
  }
  .tagline-rule {
    flex: 1;
    height: 3px;
    background: var(--brand-orange);
  }
  .tagline-text {
    font-weight: 700;
    font-size: 20px;
    letter-spacing: 5px;
    color: var(--brand-orange);
    white-space: nowrap;
  }
  .card--back {
    top: 477px;
    background: var(--card-light);
    color: var(--text-dark);
  }
  .contact-phone {
    position: absolute;
    top: 28px;
    right: 40px;
    display: flex;
    align-items: center;
    gap: 8px;
    font-size: 17px;
    letter-spacing: 0.8px;
  }
  .contact-phone svg { width: 18px; height: 18px; }
  .person {
    position: absolute;
    top: 118px;
    left: 32px;
  }
  .person-name {
    font-size: 27px;
    font-weight: 700;
    color: var(--brand-orange);
    line-height: 1;
  }
  .person-role {
    font-size: 16px;
    margin-top: 2px;
    letter-spacing: 0.6px;
  }
  .services {
    position: absolute;
    left: 118px;
    top: 206px;
    list-style: none;
    font-size: 15.5px;
    line-height: 1.4;
    letter-spacing: 0.4px;
  }
  .services li {
    position: relative;
    padding-left: 20px;
    white-space: nowrap;
  }
  .services li::before {
    content: "";
    position: absolute;
    left: 0;
    top: 5px;
    width: 12px;
    height: 12px;
    border-radius: 50%;
    background: var(--brand-orange);
  }
</style>
</head>
<body>
  <section class="card card--front" aria-label="Card front">
    <div class="brand-dot"></div>
    <div class="brand-name">HALLORAN FIELD SERVICES</div>
    <div class="tagline">
      <span class="tagline-rule"></span>
      <span class="tagline-text">CUSTOMISED SPREADING</span>
      <span class="tagline-rule"></span>
    </div>
  </section>

  <section class="card card--back" aria-label="Card back">
    <div class="contact-phone">
      <svg viewBox="0 0 24 24" aria-hidden="true">
        <path fill="#f7931e" d="M6.6 10.8a15.1 15.1 0 0 0 6.6 6.6l2.2-2.2a1 1 0 0 1 1-.25 11.4 11.4 0 0 0 3.6.57 1 1 0 0 1 1 1V20a1 1 0 0 1-1 1A17 17 0 0 1 3 4a1 1 0 0 1 1-1h3.5a1 1 0 0 1 1 1c0 1.25.2 2.45.57 3.6a1 1 0 0 1-.25 1z"/>
      </svg>
      <span>0417 552 308</span>
    </div>
    <div class="person">
      <div class="person-name">Gus</div>
      <div class="person-role">CEO/ General Manager</div>
    </div>
    <ul class="services">
      <li>Bulk fertilizer including Lime, Gypsum, Manure &amp; Compost.</li>
      <li>Granular fertilizer including Single Super,<br>Urea, Gran-am, &amp; Custom Blends.</li>
      <li>Modern equipment - Autosteer &amp; Variable Rate Capable.</li>
      <li>Friendly &amp; Reliable Service.</li>
    </ul>
  </section>
</body>
</html>
```